IT Company requires new Business Card design.

Over the years we have had a few different business card designs. We are now due for new cards across the board for all staff. We felt this would be a good time to start fresh with a new design. Our traditional card simply had our details on the front, and a list of services on the back. We don't particularly need the list of services, we have had cards where the only thing on the rear of the card was our logo.
Feel free to be creative, we would like our tag line "Complete IT Management" to appear at some point, doesn't necessarily have to be with the logo.
I have attached samples and drafts of various previous cards we have used over the years.

```html
<!DOCTYPE html>
<html lang="en">
<head>
<meta charset="utf-8">
<title>Ridgeway Networks – Business Card</title>
<link rel="stylesheet" href="https://fonts.googleapis.com/css2?family=PT+Sans:wght@400;700&display=swap">
<style>
  :root {
    --slate: #5f7380;
    --slate-dark: #4e616d;
    --ink: #3e4449;
    --paper: #ffffff;
    --backdrop: #e9e9ee;
    --rule: #b9bcc0;
  }
  * { box-sizing: border-box; margin: 0; padding: 0; }
  html, body {
    width: 1200px; height: 987px; overflow: hidden;
    background: var(--backdrop);
    font-family: "PT Sans", Arial, sans-serif;
  }
  .sheet {
    width: 1200px; height: 987px;
    display: flex; flex-direction: column;
    align-items: center; justify-content: center; gap: 56px;
  }
  .card {
    position: relative;
    width: 640px; height: 390px;
    border-radius: 28px;
    box-shadow: 0 6px 18px rgba(0,0,0,.12);
    overflow: hidden;
  }

  /* Front */
  .card--front { background: var(--paper); color: var(--ink); }
  .brand {
    position: absolute; left: 44px; top: 44px;
    display: flex; align-items: center; gap: 16px;
  }
  .brand__square { width: 64px; height: 64px; background: var(--slate); }
  .brand__name {
    font-weight: 700; color: var(--slate);
    font-size: 44px; line-height: .95; text-transform: uppercase;
  }
  .rule {
    position: absolute; left: 0; height: 2px;
    background: linear-gradient(90deg, rgba(185,188,192,0) 0%, var(--rule) 30%, var(--rule) 100%);
  }
  .rule--upper { top: 176px; width: 100%; }
  .rule--lower { top: 266px; left: 300px; right: 0; }
  .contacts {
    position: absolute; left: 36px; top: 196px;
    list-style: none; font-size: 17px; line-height: 25px;
  }
  .contacts li { display: flex; align-items: center; gap: 8px; }
  .contacts svg { width: 15px; height: 15px; fill: var(--slate); flex: none; }
  .contacts .pair { margin-left: 10px; display: inline-flex; align-items: center; gap: 6px; }
  .person {
    position: absolute; right: 36px; top: 230px; text-align: right;
  }
  .person__name { font-weight: 700; font-size: 24px; color: var(--slate); }
  .details {
    position: absolute; right: 36px; top: 276px; text-align: right;
    font-size: 19px; line-height: 25px;
  }
  .details__role { margin-bottom: 10px; }

  /* Back */
  .card--back {
    background: var(--slate); color: var(--paper);
    display: flex; flex-direction: column; align-items: center; justify-content: center; gap: 26px;
  }
  .back-brand { display: flex; align-items: center; gap: 18px; }
  .back-brand__square { width: 70px; height: 70px; background: var(--paper); }
  .back-brand__name {
    font-weight: 700; font-size: 46px; line-height: .95; text-transform: uppercase;
  }
  .tagline { font-size: 17px; letter-spacing: .32em; text-transform: uppercase; }
</style>
</head>
<body>
<main class="sheet">
  <section class="card card--front" aria-label="Card front">
    <div class="brand">
      <span class="brand__square"></span>
      <span class="brand__name">Ridgeway<br>Networks</span>
    </div>
    <div class="rule rule--upper"></div>
    <ul class="contacts">
      <li>
        <svg viewBox="0 0 16 16"><path d="M4 1l3 3-2 2c1 2 3 4 5 5l2-2 3 3-2 3C7 15 1 9 1 3z"/></svg>
        08 5550 1482
        <span class="pair"><svg viewBox="0 0 16 16"><rect x="4" y="0" width="8" height="16" rx="1.5"/></svg>0400 555 219</span>
      </li>
      <li><svg viewBox="0 0 16 16"><rect x="4" y="1" width="8" height="5"/><rect x="1" y="6" width="14" height="7" rx="1"/></svg>08 5550 1482</li>
      <li><svg viewBox="0 0 16 16"><path d="M1 3h14v10H1z M1 3l7 6 7-6" stroke="#fff" stroke-width="1"/></svg>daniel@ridgewaynetworks.com.au</li>
      <li><svg viewBox="0 0 16 16"><circle cx="8" cy="8" r="7"/></svg>www.ridgewaynetworks.com.au</li>
    </ul>
    <div class="person"><p class="person__name">Daniel Marsh</p></div>
    <div class="rule rule--lower"></div>
    <div class="details">
      <p class="details__role">Operation Manager</p>
      <p>Unit 4 12 Harbour Lane</p>
      <p>Kingsford WA 6100</p>
    </div>
  </section>

  <section class="card card--back" aria-label="Card back">
    <div class="back-brand">
      <span class="back-brand__square"></span>
      <span class="back-brand__name">Ridgeway<br>Networks</span>
    </div>
    <p class="tagline">Complete IT Management</p>
  </section>
</main>
</body>
</html>
```